Kelbrook Plumbing flyer

I want to incorporate our logo design into a new flyer promoting the business and advertising products that we install.
We install hot water systems, Air-conditioning systems and central heating systems. Along with other aspects of plumbing such as gasfitting, roofing, sanitary and drainage
I would like the background to be the same as our business cards with the water effect and colours.

Requirements
Must have
• Logo
24/7 Emergency call out
Aspects of plumbing we do
- Hot water systems
- Central Heating
- Solar hot water systems/ heat pump systems
- Gasfitting
- Drainage
- Roofing
- Air-Conditioning
Nice to have
• Pictures of hot water systems and air-conditioning system
$30 off voucher when producing this flyer (limit 1 per house hold)

```html
<!DOCTYPE html>
<html lang="en">
<head>
<meta charset="utf-8">
<title>Kelbrook Plumbing Flyer</title>
<link href="https://fonts.googleapis.com/css2?family=Montserrat:wght@500;600;700&family=Oswald:wght@400;500;600&display=swap" rel="stylesheet">
<style>
  :root {
    --stage: #4b4b4d;
    --blue: #1b8fd6;
    --blue-deep: #0d6fb4;
    --blue-bright: #2aa4f0;
    --ink: #111418;
    --dark: #1d1f22;
    --dark-2: #2b2e32;
    --white: #ffffff;
    --red: #e3141b;
    --red-deep: #b50a10;
  }
  * { margin: 0; padding: 0; box-sizing: border-box; }
  html, body { width: 1200px; height: 635px; overflow: hidden; }
  body { background: var(--stage); font-family: "Montserrat", sans-serif; position: relative; }

  .flyer {
    position: absolute; left: 389px; top: 20px;
    width: 422px; height: 595px; overflow: hidden;
    background: var(--white);
    box-shadow: 0 10px 30px rgba(0,0,0,.45);
  }
  .hero-photo {
    position: absolute; left: 0; top: 0; width: 422px; height: 290px;
    background: linear-gradient(160deg, #c9d3d8 0%, #8fa1aa 45%, #4f5e68 100%);
  }
  .swoosh { position: absolute; left: 0; top: 0; width: 422px; height: 510px; }

  .badge { position: absolute; left: 232px; top: 113px; width: 160px; height: 160px; }

  .services { position: absolute; left: 15px; top: 279px; width: 195px; }
  .services-title {
    font-family: "Oswald", sans-serif; font-weight: 400; font-size: 16px;
    color: var(--ink); letter-spacing: -.4px; line-height: 1.1;
  }
  .services-title span { color: var(--blue); font-weight: 500; }
  .service-list { list-style: none; margin-top: 14px; }
  .service-list li {
    display: flex; align-items: center; gap: 9px;
    font-size: 10px; font-weight: 600; color: var(--ink);
    line-height: 1.3; min-height: 26px;
  }
  .service-list li.two-line { min-height: 30px; }
  .service-list svg { width: 14px; height: 14px; flex: none; fill: var(--blue); }

  .intro {
    position: absolute; left: 224px; top: 305px; width: 186px;
    font-size: 9.6px; font-weight: 500; color: var(--white);
    line-height: 1.38; text-align: justify; text-align-last: center;
  }
  .work-photo {
    position: absolute; width: 92px; height: 92px; border-radius: 50%;
    border: 3px solid var(--white);
    background: radial-gradient(circle at 45% 40%, #c8d0d6 0%, #7f8d97 55%, #2f4a6a 100%);
  }
  .work-photo.one { left: 220px; top: 407px; }
  .work-photo.two { left: 320px; top: 407px; }

  .contact-bar {
    position: absolute; left: 0; top: 510px; width: 422px; height: 85px;
    background: radial-gradient(ellipse at 30% 40%, var(--dark-2), var(--dark) 70%);
    color: var(--white);
  }
  .call-label { position: absolute; left: 18px; top: 11px; font-size: 12.5px; font-weight: 600; letter-spacing: .2px; }
  .phone {
    position: absolute; left: 16px; top: 22px;
    font-family: "Oswald", sans-serif; font-weight: 500; font-size: 40px;
    color: var(--blue-bright); letter-spacing: -.5px; line-height: 1;
  }
  .contact-line {
    position: absolute; top: 68px; display: flex; align-items: center; gap: 4px;
    font-size: 7px; font-weight: 500; white-space: nowrap;
  }
  .contact-line.email { left: 18px; }
  .contact-line.web { left: 152px; }
  .contact-line svg { width: 10px; height: 10px; flex: none; }
  .brand {
    position: absolute; left: 275px; top: 28px; display: flex; align-items: center; gap: 6px;
  }
  .brand-dot { width: 20px; height: 20px; border-radius: 50%; background: var(--blue-bright); flex: none; }
  .brand-name {
    font-family: "Montserrat", sans-serif; font-weight: 700; font-size: 13px;
    color: var(--white); line-height: 1.05; text-transform: uppercase;
  }
</style>
</head>
<body>
<main class="flyer">
  <div class="hero-photo" role="img" aria-label="Smiling plumber in overalls holding a clipboard in a modern kitchen"></div>

  <svg class="swoosh" viewBox="0 0 422 510" aria-hidden="true">
    <defs>
      <linearGradient id="panelBlue" x1="0" y1="0" x2="0" y2="1">
        <stop offset="0" stop-color="#2aa4f0"/>
        <stop offset="1" stop-color="#0d6fb4"/>
      </linearGradient>
    </defs>
    <path d="M0,224 C150,246 320,223 422,108 L422,510 L0,510 Z" fill="url(#panelBlue)"/>
    <path d="M0,234 C150,256 320,233 422,120 L422,128 C320,242 150,265 0,243 Z" fill="#ffffff"/>
    <path d="M0,243 C150,265 320,242 422,131 L422,147 C320,256 150,279 0,258 Z" fill="#1d1f22"/>
    <path d="M0,258 C70,268 140,272 210,268 L210,510 L0,510 Z" fill="#ffffff"/>
  </svg>

  <svg class="badge" viewBox="0 0 160 160" role="img" aria-label="24/7 Emergency services, ready to respond">
    <defs>
      <radialGradient id="badgeRed" cx="45%" cy="40%" r="65%">
        <stop offset="0" stop-color="#ff3b3f"/>
        <stop offset="1" stop-color="#b50a10"/>
      </radialGradient>
      <path id="arcTop" d="M22,80 A58,58 0 0 1 138,80"/>
      <path id="arcBottom" d="M17,80 A63,63 0 0 0 143,80"/>
    </defs>
    <circle cx="80" cy="80" r="79" fill="#ffffff"/>
    <circle cx="80" cy="80" r="74" fill="url(#badgeRed)"/>
    <circle cx="80" cy="80" r="48" fill="none" stroke="#ffffff" stroke-width="1.5"/>
    <text font-family="Montserrat, sans-serif" font-weight="700" font-size="13" fill="#ffffff" letter-spacing="1">
      <textPath href="#arcTop" startOffset="50%" text-anchor="middle">EMERGENCY SERVICES</textPath>
    </text>
    <text font-family="Montserrat, sans-serif" font-weight="700" font-size="13" fill="#ffffff" letter-spacing="1">
      <textPath href="#arcBottom" startOffset="50%" text-anchor="middle">READY TO RESPOND</textPath>
    </text>
    <circle cx="14" cy="80" r="2.5" fill="#ffffff"/>
    <circle cx="146" cy="80" r="2.5" fill="#ffffff"/>
    <text x="80" y="96" text-anchor="middle" font-family="Oswald, sans-serif" font-weight="600" font-size="44" fill="#ffffff">24/7</text>
  </svg>

  <section class="services">
    <h2 class="services-title">ASPECTS OF PLUMBING <span>WE DO</span></h2>
    <ul class="service-list">
      <li><svg viewBox="0 0 14 14"><rect x="4" y="1" width="6" height="9" rx="1.5"/><rect x="5" y="11" width="1.2" height="3"/><rect x="7.8" y="11" width="1.2" height="3"/></svg>HOT WATER SYSTEMS</li>
      <li><svg viewBox="0 0 14 14"><path d="M1,13 V7 Q3,4 5,7 V13 H4 V7.5 Q3,6 2,7.5 V13 Z M5,13 V7 Q7,4 9,7 V13 H8 V7.5 Q7,6 6,7.5 V13 Z M9,13 V7 Q11,4 13,7 V13 H12 V7.5 Q11,6 10,7.5 V13 Z"/></svg>CENTRAL HEATING</li>
      <li class="two-line"><svg viewBox="0 0 14 14"><circle cx="9" cy="4" r="2.5"/><path d="M1,8 H13 L12,14 H2 Z"/></svg>SOLAR HOT WATER SYSTEMS/<br>HEAT PUMP SYSTEMS</li>
      <li><svg viewBox="0 0 14 14"><rect x="5" y="0.5" width="4" height="2"/><rect x="3.5" y="3" width="7" height="10.5" rx="2"/></svg>GASFITTING</li>
      <li><svg viewBox="0 0 14 14"><path d="M2,13 V7 Q2,3 6,3 H12 V7 H7 Q6,7 6,8 V13 Z"/></svg>DRAINAGE</li>
      <li><svg viewBox="0 0 14 14"><path d="M0.5,7 L7,1.5 L13.5,7 L12.5,8 L7,3.5 L1.5,8 Z"/><rect x="5.5" y="8" width="3" height="3"/></svg>ROOFING</li>
      <li><svg viewBox="0 0 14 14"><rect x="0.5" y="3" width="13" height="5" rx="1"/><rect x="3" y="10" width="1.2" height="3"/><rect x="6.4" y="10" width="1.2" height="3"/><rect x="9.8" y="10" width="1.2" height="3"/></svg>AIR-CONDITIONING</li>
    </ul>
  </section>

  <p class="intro">WE INSTALL HOT WATER SYSTEMS, AIR-CONDITIONING SYSTEMS AND CENTRAL HEATING SYSTEMS. ALONG WITH OTHER ASPECTS OF PLUMBING SUCH AS GASFITTING, ROOFING, SANITARY AND DRAINAGE</p>

  <div class="work-photo one" role="img" aria-label="Plumber fixing pipes under a sink"></div>
  <div class="work-photo two" role="img" aria-label="Plumber working on a water system with tools"></div>

  <footer class="contact-bar">
    <p class="call-label">CALL FOR MORE DETAILS</p>
    <p class="phone">0400 517 382</p>
    <p class="contact-line email">
      <svg viewBox="0 0 10 10"><circle cx="5" cy="5" r="5" fill="#2aa4f0"/><rect x="2.3" y="3.2" width="5.4" height="3.6" fill="none" stroke="#fff" stroke-width=".7"/><path d="M2.3,3.2 L5,5.3 L7.7,3.2" fill="none" stroke="#fff" stroke-width=".7"/></svg>
      info@kelbrookplumbing.com
    </p>
    <p class="contact-line web">
      <svg viewBox="0 0 10 10"><circle cx="5" cy="5" r="5" fill="#2aa4f0"/><circle cx="5" cy="5" r="2.8" fill="none" stroke="#fff" stroke-width=".6"/><path d="M2.2,5 H7.8 M5,2.2 V7.8" stroke="#fff" stroke-width=".6"/></svg>
      kelbrookplumbing.com
    </p>
    <div class="brand">
      <span class="brand-dot"></span>
      <span class="brand-name">Kelbrook<br>Plumbing</span>
    </div>
  </footer>
</main>
</body>
</html>
```